Soho based IT support firm flyer.

We need a flyer to boost our business. We're a tech support firm based in Soho, London and provide helpdesk and call out support to SMEs in and around London.
They'll be two flyers with the same design. One is location specific and has the copy:
-
1 Month Free IT Support!
Based in Soho, we provide expert tech support for both Plumbooks and PCs.
We have monthly as well as pay-as-you-go plans to fit your business.
Call us now and we'll show you how we can save you up to 50% on your IT spend.
-None location based is-
1 Month Free IT Support!
We provide expert, professional tech support for both Plumbooks and PCs.
• Dedicated full time helpdesk
• Same day onsite visits
• Proactive support with monitoring
• 98% satisfaction score*
*taken from satisfaction survey sent out on closure of every case for Oct 2011 to Oct 2012
-
The location one needs to include a map with our location marked as postcode K7R 4TB.
I'm fine with royalty photos being used within a reasonable price. Please use Pixmarrow.
Our site shows our brand best. Please keep as close to this as possible.
http://quillnet-hub.example
Thanks for looking.

```html
<!DOCTYPE html>
<html lang="en">
<head>
<meta charset="utf-8">
<title>QuillNet – Friendly &amp; Reliable Tech Support</title>
<link rel="stylesheet" href="https://fonts.googleapis.com/css2?family=Roboto+Condensed:wght@400;700&display=swap">
<style>
  :root {
    --orange: #f7941d;
    --lime: #8dc63f;
    --lime-dark: #64a22d;
    --charcoal: #2a2a2a;
    --grey-text: #6d6e71;
    --white: #ffffff;
    --photo-dark: #1d3a5c;
    --photo-light: #b9d3ea;
  }
  * { margin: 0; padding: 0; box-sizing: border-box; }
  html, body { width: 849px; height: 1200px; overflow: hidden; background: var(--white); }
  body { font-family: "Roboto Condensed", "Arial Narrow", sans-serif; }

  .flyer { position: relative; width: 849px; height: 1200px; overflow: hidden; background: var(--white); }

  .hero-photo { position: absolute; left: 0; top: 0; width: 849px; height: 520px; }
  .hero-curves { position: absolute; left: 0; top: 0; width: 849px; height: 640px; }

  .phone-tab {
    position: absolute; left: 0; top: 0; width: 339px; height: 78px;
    background: var(--orange); border-bottom-right-radius: 36px;
    display: flex; align-items: center; gap: 12px; padding-left: 26px;
    color: var(--white); font-weight: 700; font-size: 38px; letter-spacing: 0.5px;
  }
  .phone-tab svg { width: 30px; height: 30px; }

  .offer-badge {
    position: absolute; left: 56px; top: 196px; width: 204px; height: 204px;
    border-radius: 50%; background: var(--orange); border: 6px solid var(--white);
    box-shadow: 0 3px 8px rgba(0,0,0,0.25);
    display: flex; flex-direction: column; align-items: center; justify-content: center;
    color: var(--white); font-weight: 700; text-align: center; line-height: 1;
    transform: rotate(-16deg);
  }
  .offer-badge .offer-free { font-size: 62px; letter-spacing: 1px; }
  .offer-badge .offer-detail { font-size: 27px; margin-top: 4px; }

  .headline {
    position: absolute; left: 76px; top: 452px;
    color: var(--grey-text); font-weight: 700; font-size: 60px; line-height: 1.72;
  }

  .info-band { position: absolute; left: 0; top: 640px; width: 458px; height: 396px; background: var(--charcoal); }
  .benefits { list-style: none; position: absolute; left: 58px; top: 64px; width: 390px; }
  .benefits li {
    position: relative; padding-left: 32px; margin-bottom: 14px;
    color: var(--lime); font-weight: 700; font-size: 28px; line-height: 1.18;
  }
  .benefits li::before {
    content: ""; position: absolute; left: 0; top: 6px; width: 21px; height: 21px;
    border: 4px solid var(--lime); border-radius: 50%;
  }

  .contact-panel { position: absolute; left: 474px; top: 640px; width: 375px; height: 560px; background: var(--orange); }
  .location-map {
    position: absolute; left: 18px; top: 58px; width: 322px; height: 180px;
    border: 5px solid var(--white); border-radius: 8px;
    background: linear-gradient(135deg, #f3f1ec, #dcd9d2);
  }
  .address {
    position: absolute; left: 0; top: 314px; width: 375px; text-align: center;
    color: var(--white); font-size: 27px; line-height: 1.3;
  }
  .web-links { list-style: none; position: absolute; left: 48px; top: 442px; }
  .web-links li {
    display: flex; align-items: center; gap: 16px;
    color: var(--white); font-weight: 700; font-size: 23px; margin-bottom: 12px;
  }
  .web-links li::before { content: ""; width: 16px; height: 16px; background: var(--white); }

  .brand {
    position: absolute; left: 44px; top: 1082px; display: flex; align-items: center; gap: 14px;
    color: var(--lime); font-weight: 700; font-size: 76px; line-height: 1;
  }
  .brand-dot { width: 22px; height: 22px; border-radius: 50%; background: var(--lime); }
</style>
</head>
<body>
<main class="flyer">
  <svg class="hero-photo" viewBox="0 0 849 520" role="img" aria-label="Photograph of a hand touching a glowing business growth chart">
    <defs>
      <linearGradient id="photoTone" x1="0" y1="0" x2="1" y2="1">
        <stop offset="0" stop-color="#1d3a5c"/>
        <stop offset="0.55" stop-color="#5f86ad"/>
        <stop offset="1" stop-color="#b9d3ea"/>
      </linearGradient>
    </defs>
    <rect width="849" height="520" fill="url(#photoTone)"/>
  </svg>

  <svg class="hero-curves" viewBox="0 0 849 640" aria-hidden="true">
    <path d="M0,360 C200,420 500,400 849,300 L849,520 L0,520 Z" fill="#8dc63f"/>
    <path d="M300,420 C550,410 720,360 849,320 L849,400 C700,430 520,450 300,420 Z" fill="#64a22d"/>
    <path d="M0,450 C260,500 560,480 849,430 L849,640 L0,640 Z" fill="#ffffff"/>
  </svg>

  <div class="phone-tab">
    <svg viewBox="0 0 24 24" aria-hidden="true"><path fill="#fff" d="M6.6 10.8a15.2 15.2 0 0 0 6.6 6.6l2.2-2.2c.3-.3.7-.4 1-.2 1.1.4 2.3.6 3.6.6.6 0 1 .4 1 1V20c0 .6-.4 1-1 1A17 17 0 0 1 3 4c0-.6.4-1 1-1h3.5c.6 0 1 .4 1 1 0 1.3.2 2.5.6 3.6.1.3 0 .7-.2 1L6.6 10.8z"/></svg>
    <span>0207 555 0148</span>
  </div>

  <div class="offer-badge">
    <span class="offer-free">FREE</span>
    <span class="offer-detail">One Month</span>
    <span class="offer-detail">IT Support!</span>
  </div>

  <h1 class="headline">Friendly &amp;<br>Reliable Tech Support</h1>

  <section class="info-band">
    <ul class="benefits">
      <li>Based in Soho, we provide expert tech support for both Plumbooks and PCs.</li>
      <li>We have monthly as well as pay-as-you-go plans to fit your business.</li>
      <li>Call us now and we’ll show you how we can save you up to 50% on your IT spend.</li>
    </ul>
  </section>

  <section class="contact-panel">
    <div class="location-map" role="img" aria-label="Street map of Soho with the office location marked"></div>
    <p class="address">12-14 Marlow Court,<br>Wardour Row,<br>London K7R 4TB</p>
    <ul class="web-links">
      <li>info@quillnet-hub.example</li>
      <li>www.quillnet-hub.example</li>
    </ul>
  </section>

  <div class="brand"><span>QuillNet</span><span class="brand-dot"></span></div>
</main>
</body>
</html>
```